LADIES' HARBOR COLLECTIVE

Design a website for a membership based organization focusing on entrepreneurship, women's issues and global news regarding commerce.
Also, want a news daily tie in to site, and social media outlets.
I want the colors in strong blue, deep or metallic gold and cream/white like logo which will be provided. I want logo altered with globe to replace small sphere in the design.
Also, board members page that should be redesigned. Might need extra coding.
PLEASE SEE http://ladiesharborcollective.example DIDN'T LIKE THIS LAY OUT AT ALL TOO MUCH WHITE AND NOT ENOUGH IMPACT. WANT TO DRAW MEMBERS.

PLEASE SEE http://www.qrtv-sample.example/Index.cfm BUT THIS IS WAY TO BUSY BUT I LIKE THE SLIDING.

SEE OUR TWITTER ACCOUNT FOR INSIGHT. @LADIESHARBCOL

Reason: Happy Holidays. The board approving the design will be out on season time vacation until Jan. 2. Please make any edits requested from designer already submitting layouts. Thank you, Odette

Target Market(s)

GLOBAL BUSINESS WOMEN AND ENTREPRENEURS AGES 20-65

Industry/Entity Type

Media

Number of Pages Required

4 page

Font styles to use
Other font styles liked:
• Baskerville or something similar

Colors
fbed22
3377b5
9bcb3c

Requirements
Must have
• Show diversity of ethnicities if using stock photos. Vibrant and inviting site, MUST JOIN or Be part of this organization. Luxury style
• THIS IS A FOR PROFIT WEBSITE.
• Membership Fees:
• Annual Fee $250
• For an additional fee of $150 you can grow your visibility and voice through our Ladies' Harbor Collective Bulletin and Speaker's Bureau (LHCBSB).
• LHC Speaker's Bureau will support your personal, business and organizations' objectives and to give you greater visibility and voice as an authority world leader or business visionary in your field of service.
• LHCSB realizes that so many worthy leaders' in diverse fields of service are never allowed to be heard. If you feel you are a dynamic speaker, run a worthwhile business or organization and whose wisdom and success can be of service of others sign up today and be part of the LHCSB!
• Student Membership
• Discounted student memberships are also available. Students have access to selected group forums, as well as selected groups of members that provide mentoring. Mentoring helps continue the member's legacy and creates a well spring of future leaders. Student membership fees cost just $75 a year.
• Contact us to help promote you and other women's vision throughout the world.
• Join LHC Now!
• CAN YOU PROVIDE A HEADLINE WITHOUT WOMEN SEE TWITTER ACCOUNT.
Nice to have
• Nice headline and well position tabs.
• Home
• Join LHC Now
• Memberships
• LHC Team Leadership
• About Us
• Contact
• LHC is an Effective Women's Initiative for You!
• New Member - Women's Organization
• 20% Discount- Offer Valid on Your Membership Fee When You Join before 1/30/2105
• Memberships
• LHC Leadership
• At Ladies' Harbor Collective, we offer the opportunity to connect with women throughout the globe. Join these trailblazers to shorten your path to success and camaraderie.
• Who We Are
• Ladies' Harbor Collective is an online women's initiative that promotes your business and visions through social engagement. We are here to help you form strategic partnerships with like-minded women around the world. End your solo journey by becoming a member of LHC.
• LHC also features a forum to promote the services, campaigns, and social activism by our members.
• LHC is about women helping other women. Contact us for more information.
• Learn More about Ladies' Harbor Collective
• Contact us for more information in regards to LHC membership and how to get involved.
• SHARE THIS PAGE:
• twitter, fb, instagram, etc.

```html
<!DOCTYPE html>
<html lang="en">
<head>
<meta charset="utf-8">
<title>Ladies' Harbor Collective</title>
<link rel="stylesheet" href="https://fonts.googleapis.com/css2?family=Roboto:wght@400;500;700&family=Roboto+Condensed:wght@400&display=swap">
<style>
:root{
  --page-blue:#0c6cc0;
  --brand-blue:#1a70b9;
  --gold:#fbbd18;
  --gold-dark:#e3a70c;
  --ink:#222;
  --text:#454545;
  --muted:#888;
  --line:#c4c4c4;
  --white:#fff;
  --arrow-grey:#bdbdbd;
}
*{box-sizing:border-box;margin:0;padding:0}
html,body{width:1084px;height:1200px;overflow:hidden;background:var(--page-blue);font-family:"Roboto",Arial,sans-serif;color:var(--text)}
.stage{position:absolute;left:0;top:0;width:1170px;height:1295px;transform:scale(0.9265);transform-origin:0 0}
.page{position:absolute;left:98px;top:5px;width:974px;height:1285px;background:var(--white)}
.abs{position:absolute}
/* header */
.brand{left:10px;top:20px;width:220px;height:130px}
.brand-mark{position:absolute;left:88px;top:10px;width:40px;height:40px;border-radius:50%;background:var(--gold)}
.brand-name{position:absolute;left:0;top:96px;font-size:19.5px;color:#333;letter-spacing:-0.6px;white-space:nowrap}
.brand-tag{position:absolute;left:2px;top:120px;font-size:7.2px;font-weight:500;color:#333;white-space:nowrap}
.member-strip{left:305px;top:20px;width:445px;height:81px;background:linear-gradient(90deg,#e9d6c6,#b88a6a 30%,#efe2d6 55%,#9c6c55 75%,#f0e6de)}
.search{left:779px;top:30px;width:186px;height:41px;border:1px solid #ddd;display:flex}
.search span{flex:1;font-size:12px;color:#555;padding:14px 0 0 14px}
.search b{width:37px;background:var(--brand-blue);display:flex;align-items:center;justify-content:center}
.main-nav{left:305px;top:101px;width:661px;height:49px;background:var(--gold);display:flex}
.main-nav a{display:flex;align-items:center;justify-content:center;font-size:13px;color:#2a2a2a;text-decoration:none;border-right:1px solid rgba(255,255,255,.7)}
.main-nav a:last-child{border-right:0}
.main-nav a.active{background:var(--gold-dark)}
/* hero */
.hero{left:9px;top:160px;width:957px;height:338px;background:radial-gradient(circle at 62% 35%,#2f6b98 0%,#1d4163 45%,#142a40 100%);box-shadow:0 8px 8px -6px rgba(0,0,0,.35)}
.hero-title{position:absolute;left:723px;top:28px;width:210px;font-family:"Roboto Condensed",Arial,sans-serif;font-size:30px;line-height:36px;color:var(--white)}
.hero-dots{position:absolute;left:439px;top:304px;display:flex;gap:3px}
.hero-dots i{width:17px;height:17px;border-radius:50%;background:var(--white);border:1px solid #999;display:block;position:relative}
.hero-dots i.on::after{content:"";position:absolute;left:4px;top:4px;width:7px;height:7px;border-radius:50%;background:var(--brand-blue)}
/* feature cards */
.card{width:470px;height:117px;border:1px solid var(--line);top:520px}
.card-icon{position:absolute;left:32px;top:29px;width:60px;height:60px;border-radius:50%;background:var(--gold);display:flex;align-items:center;justify-content:center}
.card h3{position:absolute;left:130px;font-size:16px;font-weight:400;color:var(--brand-blue)}
.card p{position:absolute;left:130px;width:270px;font-size:12.6px;line-height:18px;color:var(--text)}
/* section headings */
.section-title{font-size:16px;font-weight:400;color:var(--brand-blue)}
.section-title.small{font-size:14px;font-weight:500}
.photo{background:linear-gradient(160deg,#9bb7d6,#6e8d5a 55%,#c6c9bb)}
.about-text{left:341px;top:681px;width:282px;font-size:12.7px;line-height:20px}
.btn{background:var(--gold);font-size:12px;color:#222;display:flex;align-items:center;justify-content:center}
.pager{display:flex;gap:2px}
.pager i{width:22px;height:22px;background:var(--arrow-grey);display:flex;align-items:center;justify-content:center}
.event{width:190px;top:934px}
.event .pic{height:160px}
.event p{margin-top:9px;font-size:12px;line-height:18px;text-transform:uppercase;color:var(--ink)}
/* tweets */
.feed{left:657px;top:656px;width:306px;height:402px;border:2px solid var(--gold)}
.feed-head{position:absolute;left:14px;top:16px}
.feed-head .n{font-size:17px;color:#333;letter-spacing:-0.5px}
.feed-head .t{font-size:6.8px;font-weight:500;color:#333}
.feed-dot{position:absolute;right:12px;top:22px;width:20px;height:20px;border-radius:50%;background:#3aa3e3}
.tweet{position:absolute;left:0;width:296px;padding:0 12px 0 14px}
.tweet+.tweet{border-top:1px solid #ddd}
.avatar{position:absolute;left:14px;top:0;width:40px;height:40px;background:linear-gradient(#b9a08c,#5d4a3f)}
.who{position:absolute;left:64px;top:5px;font-size:13px;color:#222;line-height:15px}
.who span{display:block;color:var(--brand-blue)}
.when{position:absolute;right:8px;top:5px;font-size:12px;color:#444}
.msg{position:absolute;left:14px;width:272px;font-size:11.2px;line-height:16px;color:#444}
.input{left:659px;top:1108px;width:254px;height:40px;border:1px solid #ccc;font-size:12px;color:#444;padding:13px 0 0 13px}
/* footer */
.footer{left:0;top:1181px;width:974px;height:104px;background:linear-gradient(#ececec,#fff)}
.follow{position:absolute;left:25px;top:25px;font-size:13px;color:#333}
.socials{position:absolute;left:26px;top:50px;display:flex;gap:9px}
.socials i{width:12px;height:12px;border-radius:50%;background:#333;display:block}
.foot-nav{position:absolute;right:22px;top:25px;font-size:13px;color:#444;word-spacing:1px}
.copy{position:absolute;right:22px;top:49px;font-size:13px;color:#333}
</style>
</head>
<body>
<div class="stage">
  <div class="page">
    <header>
      <div class="abs brand">
        <i class="brand-mark"></i>
        <div class="brand-name">Ladies' Harbor Collective</div>
        <div class="brand-tag">PROFITABLE AND PURPOSEFUL SOCIAL ENGAGEMENT</div>
      </div>
      <div class="abs member-strip" role="img" aria-label="Row of diverse women members smiling"></div>
      <div class="abs search"><span>SEARCH</span><b><svg width="10" height="14" viewBox="0 0 10 14"><path d="M2 1l6 6-6 6" fill="none" stroke="#fff" stroke-width="2"/></svg></b></div>
      <nav class="abs main-nav">
        <a class="active" style="width:86px">HOME</a>
        <a style="width:109px">ABOUT US</a>
        <a style="width:99px">SERVICES</a>
        <a style="width:116px">WHO WE ARE</a>
        <a style="width:130px">MEMBERSHIPS</a>
        <a style="width:121px">CONTACT US</a>
      </nav>
    </header>

    <section class="abs hero" role="img" aria-label="Smiling woman working on a laptop with a glowing network of social icons over a world map">
      <h1 class="hero-title">Ladies' Harbor Collective is an online women's initiative</h1>
      <div class="hero-dots"><i></i><i class="on"></i><i></i><i></i></div>
    </section>

    <section class="abs card" style="left:12px">
      <div class="card-icon"><svg width="22" height="22" viewBox="0 0 22 22"><circle cx="11" cy="6" r="5" fill="#fff"/><path d="M2 21c0-6 4-8 9-8s9 2 9 8z" fill="#fff"/></svg></div>
      <h3 style="top:20px">MEMBERSHIPS</h3>
      <p style="top:42px">At Ladies' Harbor Collective, we offer the opportunity to connect with women throughout the globe.</p>
    </section>
    <section class="abs card" style="left:494px">
      <div class="card-icon"><svg width="28" height="22" viewBox="0 0 28 22"><circle cx="14" cy="6" r="4.5" fill="#fff"/><circle cx="6" cy="8" r="3.5" fill="#fff"/><circle cx="22" cy="8" r="3.5" fill="#fff"/><path d="M7 21c0-6 3-8 7-8s7 2 7 8z M0 20c0-5 2-7 6-7 1 0 2 .2 2.5 .5-1.5 1.5-2.5 4-2.5 6.5z M28 20c0-5-2-7-6-7-1 0-2 .2-2.5 .5 1.5 1.5 2.5 4 2.5 6.5z" fill="#fff"/></svg></div>
      <h3 style="top:26px">LHC LEADERSHIP</h3>
      <p style="top:48px">Join these trailblazers to shorten your path to success and camaraderie.</p>
    </section>

    <h2 class="abs section-title" style="left:12px;top:660px">WHO WE ARE</h2>
    <div class="abs photo" style="left:13px;top:686px;width:309px;height:187px" role="img" aria-label="Member waving outdoors in a parking lot"></div>
    <p class="abs about-text">Ladies' Harbor Collective is an online women's initiative that promotes your business and visions through social engagement. We are here to help you form strategic partnerships with like-minded women around the world. End your solo journey by becoming a member of LHC.</p>
    <div class="abs btn" style="left:345px;top:846px;width:101px;height:28px">READ MORE</div>

    <h2 class="abs section-title small" style="left:13px;top:907px">LATEST EVENTS</h2>
    <div class="abs pager" style="left:580px;top:904px">
      <i><svg width="8" height="10" viewBox="0 0 8 10"><path d="M6 1L2 5l4 4" fill="none" stroke="#222" stroke-width="1.6"/></svg></i>
      <i><svg width="8" height="10" viewBox="0 0 8 10"><path d="M2 1l4 4-4 4" fill="none" stroke="#222" stroke-width="1.6"/></svg></i>
    </div>
    <article class="abs event" style="left:15px"><div class="pic" style="background:linear-gradient(#2a2320,#6b4a3a)" role="img" aria-label="Portrait of a woman speaker"></div><p>LHC also features a forum to promote the services.</p></article>
    <article class="abs event" style="left:225px"><div class="pic" style="background:linear-gradient(#3a3a3a,#9a9a9a)" role="img" aria-label="Black and white crowd at a rally"></div><p>Contrary to popular belief, Lorem Ipsum is not simply random text. It has roots</p></article>
    <article class="abs event" style="left:437px"><div class="pic" style="background:linear-gradient(#0d1a3a,#2a5fb0 50%,#5a1a1a)" role="img" aria-label="Illuminated city billboard tower at night"></div><p>The standard chunk of Lorem Ipsum used since the 1500s is reproduced.</p></article>

    <aside class="abs feed">
      <div class="feed-head"><div class="n">Ladies' Harbor Collective</div><div class="t">PROFITABLE AND PURPOSEFUL SOCIAL ENGAGEMENT</div></div>
      <i class="feed-dot"></i>
      <div class="tweet" style="top:57px;border-top:1px solid #ccc;height:110px;padding-top:0">
        <div class="avatar" style="top:12px" role="img" aria-label="Profile photo"></div>
        <div class="who" style="top:17px">RENATA VALE OSEI<span>@RENATAVALEO</span></div>
        <div class="when" style="top:17px">1h</div>
        <p class="msg" style="top:54px">By studiofernline1 "#tbt Renata Vale Osei with Dario Mensah at the product launch for Keep Your Curl.</p>
      </div>
      <div class="tweet" style="top:167px;height:99px">
        <div class="avatar" style="top:10px;background:linear-gradient(#555,#222)" role="img" aria-label="Profile photo"></div>
        <div class="who" style="top:15px">CALLUM BRISK<span>@CALLUM_BRISK</span></div>
        <div class="when" style="top:15px">5h</div>
        <p class="msg" style="top:55px">@JunaHalvorsen @TradeLedger I've always pref'd wrkin 4 fem leaders ovr male. Patience, encouragement.</p>
      </div>
      <div class="tweet" style="top:266px;height:90px">
        <div class="avatar" style="top:10px;background:linear-gradient(#c9a58a,#7a5a44)" role="img" aria-label="Profile photo"></div>
        <div class="who" style="top:15px">IVO MARCHETTI<span>@IVOMARCH1994</span></div>
        <div class="when" style="top:15px">10h</div>
        <p class="msg" style="top:55px">@JunaHalvorsen @TradeLedger I've always pref'd wrkin 4 fem leaders ovr male. Patience, encouragement.</p>
      </div>
      <div class="pager" style="position:absolute;left:247px;top:364px">
        <i><svg width="8" height="10" viewBox="0 0 8 10"><path d="M6 1L2 5l4 4" fill="none" stroke="#222" stroke-width="1.6"/></svg></i>
        <i><svg width="8" height="10" viewBox="0 0 8 10"><path d="M2 1l4 4-4 4" fill="none" stroke="#222" stroke-width="1.6"/></svg></i>
      </div>
    </aside>

    <h2 class="abs section-title small" style="left:658px;top:1084px">NEWSLETTER SIGNUP</h2>
    <div class="abs input">Email address</div>
    <div class="abs btn" style="left:923px;top:1108px;width:36px;height:40px"><svg width="12" height="18" viewBox="0 0 12 18"><path d="M2 2l7 7-7 7" fill="none" stroke="#fff" stroke-width="2.6"/></svg></div>

    <footer class="abs footer">
      <div class="follow">Follow us on</div>
      <div class="socials"><i></i><i></i><i></i></div>
      <div class="foot-nav">HOME &nbsp;| &nbsp;ABOUT US &nbsp;| &nbsp;SERVICES &nbsp;| &nbsp;WHO WE ARE &nbsp;| &nbsp;MEMBERSHIPS &nbsp;| &nbsp;CONTACT</div>
      <div class="copy">Copyrights @ 2014 All Rights Reserved</div>
    </footer>
  </div>
</div>
</body>
</html>
```